WeatheredOnward.net wordpress design

Concept: Website where personal stories, personal videos can be posted as a challenge while awaiting the wisdom of experience from others who have survived this same event or challenge in their lifetime.
Support aspects will be in 4 quadrants of Challenges:
1. Financial 2. Medical & Physical
3. Legal Matters 4. Psychological & Spiritual - ability to chat online with a spiritual/psychological counselor or life coach
Updates
Project Deadline Extended
Reason: Bit more time to complete designs.
Wanted to thank all of you for your designs! Greatly appreciated. Very creative ideas that captured the essence of this website. Will be back with a selection very shortly.
Target Market(s)
Anyone looking for a solution based upon experiential wisdom
Industry/Entity Type
Financial
Requirements
Must have
- Interactive website: Where you can post a challenge or issue via a written question or a video and ask for a solution.
Ability to access any of the 4 Quadrants (as listed above) to ask for an expert, via experience, advice and wisdom from those who have similar challenges.

```html
<!DOCTYPE html>
<html lang="en">
<head>
<meta charset="utf-8">
<title>WeatheredOnward.net</title>
<link rel="stylesheet" href="https://fonts.googleapis.com/css2?family=Questrial&family=Mulish:wght@400;700;800&display=swap">
<style>
:root{
  --amber:#f5b400;
  --amber-dark:#e39a00;
  --ink:#111;
  --text:#555;
  --muted:#777;
  --meta:#d98c00;
  --night:#1c1c1c;
  --paper:#fff;
  --mist:#e3e3e3;
  --field:#f7f7f7;
  --line:#cfcfcf;
}
*{box-sizing:border-box;margin:0;padding:0}
html,body{width:1063px;height:1200px;overflow:hidden}
body{font-family:"Questrial",sans-serif;color:var(--text);background:var(--mist);position:relative}
.masthead{position:absolute;left:0;top:0;width:1063px;height:441px;border-top:3px solid var(--amber);
  background:radial-gradient(ellipse at 50% 10%,#333 0%,#1e1e1e 55%,#141414 100%)}
.account{position:absolute;left:857px;top:0;width:109px;height:23px;background:var(--amber);border-radius:0 0 4px 4px;
  font:700 10px "Mulish",sans-serif;color:var(--ink);display:flex;justify-content:center;align-items:center;gap:12px}
.account a{color:var(--ink)}
.brand{position:absolute;left:126px;top:33px;width:161px;height:73px;background:var(--paper);border-radius:4px;
  display:flex;align-items:center;gap:7px;padding:0 9px}
.brand-mark{width:20px;height:20px;background:var(--amber);flex:none}
.brand-name{font:700 10.5px "Mulish",sans-serif;color:var(--amber-dark);white-space:nowrap}
.nav{position:absolute;left:126px;top:136px;width:840px;height:27px;background:linear-gradient(#ffc21a,var(--amber-dark));
  border-radius:3px 3px 0 0;display:flex;align-items:center;font-size:13px;color:#222}
.nav a{color:#222;text-decoration:none;padding:0 22px}
.nav .current{background:var(--paper);height:27px;display:flex;align-items:center;width:81px;justify-content:center;
  font-family:"Mulish",sans-serif;font-weight:700;border-radius:3px 0 0 0;padding:0}
.search{margin-left:auto;margin-right:6px;display:flex}
.search span{width:130px;height:17px;background:var(--paper);font-size:10px;color:#aaa;padding:2px 5px}
.search b{width:22px;height:17px;background:#111;color:#fff;font:800 10px "Mulish",sans-serif;display:flex;align-items:center;justify-content:center}
.showcase{position:absolute;left:126px;top:163px;width:840px;height:325px;background:var(--paper);border-radius:0 0 4px 4px;
  box-shadow:0 6px 10px rgba(0,0,0,.08)}
.hero{position:absolute;left:8px;top:6px;width:583px;height:312px}
.hero-photo{position:absolute;left:0;top:0;width:583px;height:271px;background:linear-gradient(135deg,#2b2f2d,#121413 60%,#262a28)}
.hero-caption{position:absolute;right:8px;top:277px;text-align:left}
.hero-caption h2{font:400 19px "Questrial",sans-serif;color:#111;line-height:1}
.hero-caption h2 strong{font-family:"Mulish",sans-serif;font-weight:800}
.hero-caption p{font-size:10.5px;color:#333;margin-top:2px}
.dots{position:absolute;left:16px;top:302px;display:flex;gap:5px}
.dots i{width:7px;height:7px;border-radius:50%;background:#ddd}
.dots i:first-child{background:var(--amber)}
.ask{position:absolute;left:609px;top:34px;width:222px}
.ask h3{font:400 19px "Questrial",sans-serif;color:#444;margin-top:-20px}
.ask p{font-size:11.5px;color:#555;line-height:1.2;margin-top:7px}
.field{border:1px solid var(--line);border-radius:4px;background:var(--field);height:23px;font-size:11px;color:#999;padding:4px 6px;margin-top:5px}
.field.first{margin-top:17px}
.field.tall{height:92px}
.row{display:flex;gap:6px}
.row .field:first-child{flex:1}
.row .field:last-child{width:63px;text-align:center}
.cta{display:flex;align-items:center;justify-content:center;height:23px;margin-top:5px;background:linear-gradient(#3a3a3a,#0c0c0c);
  color:#fff;font:700 11.5px "Mulish",sans-serif;border-radius:3px}
.content{position:absolute;left:126px;top:516px;width:840px;height:642px;background:var(--paper);border-radius:3px}
.section-title{position:absolute;font:400 19px "Questrial",sans-serif;color:#444}
.rule{position:absolute;height:10px;background:radial-gradient(ellipse at 50% 0,rgba(0,0,0,.1),transparent 70%)}
.article{position:absolute;left:16px;width:372px}
.article h4,.quad h4{font:700 13.5px "Mulish",sans-serif;color:#111}
.article .meta{font:700 9.5px "Mulish",sans-serif;color:var(--meta);line-height:1.3;letter-spacing:.3px}
.share{display:flex;gap:2px;margin:3px 0}
.share i{width:14px;height:14px;border-radius:2px}
.article p{font-size:10.5px;line-height:1.28;color:#555}
.more{display:inline-block;background:#8a8a8a;color:#fff;font-size:10px;border-radius:4px;padding:1px 8px;margin-top:2px}
.quad{position:absolute;width:170px}
.quad h4{font-size:15px;line-height:1.2;margin-bottom:9px}
.entry{margin-bottom:5px;font-size:10.5px;line-height:1.25;color:#777}
.entry b{display:block;font:700 10.5px "Mulish",sans-serif;color:#555}
.chat{position:absolute;left:482px;top:512px;width:230px}
.chat h3{font:400 19px "Questrial",sans-serif;color:#444;line-height:1.15}
.chat p{font-size:11.5px;color:#555;line-height:1.2;margin-top:8px;width:220px}
.chat .cta{width:220px;height:22px;margin-top:8px}
</style>
</head>
<body>
<header class="masthead">
  <div class="account"><a>Login</a><span>|</span><a>Register</a></div>
  <div class="brand"><span class="brand-mark"></span><span class="brand-name">WeatheredOnward.net</span></div>
  <nav class="nav">
    <a class="current">Home</a><a>Profile</a><a>Followers</a><a>My Uploads</a>
    <div class="search"><span>search</span><b>Go</b></div>
  </nav>
</header>

<section class="showcase">
  <div class="hero">
    <div class="hero-photo" role="img" aria-label="Photo of a student scratching his head in front of a chalkboard full of equations"></div>
    <div class="hero-caption"><h2>Learn from <strong>Experience</strong></h2><p>Experience is the best teacher overall</p></div>
    <div class="dots"><i></i><i></i><i></i><i></i><i></i></div>
  </div>
  <form class="ask">
    <h3>Ask your Question</h3>
    <p>and get answered by the experienced people around the world</p>
    <div class="field first">Name</div>
    <div class="field">email address</div>
    <div class="field tall">your question</div>
    <div class="field">Select Quadrant</div>
    <div class="row"><div class="field">Upload Video (optional)</div><div class="field">Browse</div></div>
    <div class="cta">Get Answer</div>
  </form>
</section>

<main class="content">
  <h2 class="section-title" style="left:15px;top:12px">Fresh Articles</h2>
  <h2 class="section-title" style="left:484px;top:12px">Browse by Quadrant</h2>
  <div class="rule" style="left:40px;top:42px;width:760px"></div>

  <article class="article" style="top:65px">
    <h4>Problem in life with Money</h4>
    <div class="meta">July 13, 2012<br>132 response, 8996 views</div>
    <div class="share"><i style="background:#f28a1e"></i><i style="background:#f6a623"></i><i style="background:#3b5998"></i><i style="background:#9bbbd8"></i><i style="background:#2aa9e0"></i><i style="background:#e63a8a"></i></div>
    <p>This is Pixelforge's version of Lorem Ipsum. Proin gravida nibh vel velit auctor aliquet. Aenean sollicitudin, lorem quis bibendum auctor, nisi elit consequat ipsum, nec sagittis sem nibh id elit. Duis sed ...</p>
    <span class="more">more</span>
  </article>
  <article class="article" style="top:208px">
    <h4>Problem in life with Money</h4>
    <div class="meta">July 13, 2012<br>132 response, 8996 views</div>
    <div class="share"><i style="background:#f28a1e"></i><i style="background:#f6a623"></i><i style="background:#3b5998"></i><i style="background:#9bbbd8"></i><i style="background:#2aa9e0"></i><i style="background:#e63a8a"></i></div>
    <p>This is Pixelforge's version of Lorem Ipsum. Proin gravida nibh vel velit auctor aliquet. Aenean sollicitudin, lorem quis bibendum auctor, nisi elit consequat ipsum, nec sagittis sem nibh id elit. Duis sed ...</p>
    <span class="more">more</span>
  </article>
  <article class="article" style="top:350px">
    <h4>Problem in life with Money</h4>
    <div class="meta">July 13, 2012<br>132 response, 8996 views</div>
    <div class="share"><i style="background:#f28a1e"></i><i style="background:#f6a623"></i><i style="background:#3b5998"></i><i style="background:#9bbbd8"></i><i style="background:#2aa9e0"></i><i style="background:#e63a8a"></i></div>
    <p>This is Pixelforge's version of Lorem Ipsum. Proin gravida nibh vel velit auctor aliquet. Aenean sollicitudin, lorem quis bibendum auctor, nisi elit consequat ipsum, nec sagittis sem nibh id elit. Duis sed ...</p>
    <span class="more">more</span>
  </article>
  <article class="article" style="top:493px">
    <h4>Problem in life with Money</h4>
    <div class="meta">July 13, 2012<br>132 response, 8996 views</div>
    <div class="share"><i style="background:#f28a1e"></i><i style="background:#f6a623"></i><i style="background:#3b5998"></i><i style="background:#9bbbd8"></i><i style="background:#2aa9e0"></i><i style="background:#e63a8a"></i></div>
    <p>This is Pixelforge's version of Lorem Ipsum. Proin gravida nibh vel velit auctor aliquet. Aenean sollicitudin, lorem quis bibendum auctor, nisi elit consequat ipsum, nec sagittis sem nibh id elit. Duis sed ...</p>
    <span class="more">more</span>
  </article>

  <section class="quad" style="left:483px;top:71px">
    <h4>Financial Problems</h4>
    <div class="entry"><b>Problem in life with Money</b>July 13, 2012<br>132 response, 8996 views</div>
    <div class="entry"><b>Problem in life with Money</b>July 13, 2012<br>132 response, 8996 views</div>
    <div class="entry"><b>Problem in life with Money</b>July 13, 2012<br>132 response, 8996 views</div>
    <span class="more">more</span>
  </section>
  <section class="quad" style="left:671px;top:71px">
    <h4>Legal Matters</h4>
    <div class="entry"><b>Problem in life with Money</b>July 13, 2012<br>132 response, 8996 views</div>
    <div class="entry"><b>Problem in life with Money</b>July 13, 2012<br>132 response, 8996 views</div>
    <div class="entry"><b>Problem in life with Money</b>July 13, 2012<br>132 response, 8996 views</div>
    <span class="more">more</span>
  </section>
  <section class="quad" style="left:483px;top:291px">
    <h4>Medical &amp; Physical</h4>
    <div class="entry"><b>Problem in life with Money</b>July 13, 2012<br>132 response, 8996 views</div>
    <div class="entry"><b>Problem in life with Money</b>July 13, 2012<br>132 response, 8996 views</div>
    <div class="entry"><b>Problem in life with Money</b>July 13, 2012<br>132 response, 8996 views</div>
    <span class="more">more</span>
  </section>
  <section class="quad" style="left:671px;top:291px">
    <h4>Psychological &amp;<br>Spiritual</h4>
    <div class="entry"><b>Problem in life with Money</b>July 13, 2012<br>132 response, 8996 views</div>
    <div class="entry"><b>Problem in life with Money</b>July 13, 2012<br>132 response, 8996 views</div>
    <span class="more">more</span>
  </section>

  <div class="rule" style="left:490px;top:497px;width:320px"></div>
  <section class="chat">
    <h3>Chat Online with a<br>Life Coach</h3>
    <p>and get answered by the experienced<br>people around the world</p>
    <div class="cta">Start Now</div>
  </section>
</main>
</body>
</html>
```